Electric mountain bike tours nz

We are an Electric Mountain bike tour company in New Zealand. We will be offering bike rental and guided tours around the Nelson region in New Zealand. I want our website to represent both Mountain biking and New Zealand with the colours layout and features. We want tabs for the following:
-1 about us
-2 what we offer
-3 bookings/contact
Under the about us tab will be who we are as a a company. I want the ability to add videos to each of these tabs as we move foward with videos of the tracks we will be riding. I want the website to be editable so I can add and remove videos/photos myself. Also "our bikes" will be under this tab.
Under the what we offer tab will be
-1 bike rental and pricing
-2 guided tours and pricing
-3 recommended package deals.
I want to able to put the tracks under the guided tours tab and select beginner/ intermediate/advanced and have the tracks in each of the following to match the rider level. Also to be able to have a small video of the track would be great in this section.
Bookings and contact tab
(Further information for this tab to be updated soon)
Coded - Design and coding required
1 page
- Silver ferns, kiwi, mountains

```html
<!DOCTYPE html>
<html lang="en">
<head>
<meta charset="utf-8">
<title>TRAILWAKA – Electric Mountain Bike Tours</title>
<link rel="stylesheet" href="https://fonts.googleapis.com/css2?family=Montserrat:wght@400;500;600;700&family=Lato:ital,wght@0,700;0,900;1,900&family=Open+Sans:wght@400;600;700&display=swap">
<style>
:root{
  --ink:#111;
  --white:#fff;
  --blue:#1d8bf0;
  --blue-dark:#0f63d6;
  --green:#1f9a2b;
  --green-dark:#137a1e;
  --orange:#f26a1b;
  --orange-light:#f79150;
  --standard:#2f8f3e;
  --standard-light:#49a257;
  --ultimate:#2747b8;
  --ultimate-light:#4364cf;
  --card:#2a2a2a;
  --card-line:#3b3b3b;
  --grey-text:#555;
  --star:#f1b70e;
  --footer:#dcdcdc;
}
*{margin:0;padding:0;box-sizing:border-box}
html,body{width:1200px;height:3543px;overflow:hidden}
body{position:relative;font-family:"Open Sans",sans-serif;color:var(--ink);background:var(--white)}
.abs{position:absolute}
.heading{font-family:"Montserrat",sans-serif;font-weight:500;letter-spacing:1px}
.pill{display:inline-block;border-radius:40px;font-family:"Open Sans",sans-serif;font-weight:600;text-align:center}

/* nav */
.topbar{left:0;top:0;width:1200px;height:95px;background:#000;z-index:3}
.brand{left:190px;top:5px;width:156px;height:156px;border-radius:50%;background:#000;z-index:4;display:flex;align-items:center;justify-content:center;border:4px solid var(--white)}
.brand span{font-family:"Montserrat",sans-serif;font-weight:700;font-size:25px;color:var(--white);letter-spacing:1px}
.main-nav{left:536px;top:48px;display:flex;gap:31px;z-index:4}
.main-nav a{color:var(--white);font-family:"Montserrat",sans-serif;font-size:14px;font-weight:500;text-decoration:none}

/* hero */
.hero{left:0;top:95px;width:1200px;height:625px;background:linear-gradient(180deg,#6b8fae 0%,#8aa6b8 25%,#3c4e3a 50%,#27321f 75%,#1d2416 100%)}
.hero-title{left:0;top:262px;width:1200px;text-align:center;color:var(--white);font-family:"Montserrat",sans-serif;font-weight:500;font-size:42px;line-height:46px;letter-spacing:1px}
.hero-btn{left:522px;top:363px;width:166px;height:44px;line-height:44px;background:var(--blue);color:var(--white);font-size:16px}
.dots{left:1072px;top:325px;display:flex;flex-direction:column;gap:10px}
.dots i{width:12px;height:12px;border-radius:50%;background:var(--white);display:block}
.dots i.off{background:transparent;border:2px solid var(--white)}

/* about */
.about-title{left:0;top:762px;width:1200px;text-align:center;font-size:34px}
.about-copy{left:310px;top:822px;width:580px;text-align:center;font-size:13px;line-height:22px;color:var(--grey-text)}
.about-copy p+p{margin-top:14px}
.about-btn{left:522px;top:998px;width:166px;height:44px;line-height:44px;background:var(--blue-dark);color:var(--white);font-size:16px}
.fern{opacity:.35}

/* video */
.video-band{left:0;top:1170px;width:1200px;height:490px}
.video-title{left:205px;top:1305px;color:var(--white);font-size:26px}
.video-copy{left:208px;top:1355px;width:320px;color:var(--white);font-size:13px;line-height:24px}
.video-btn{left:208px;top:1502px;width:168px;height:44px;line-height:40px;border:2px solid var(--white);color:var(--white);font-size:16px}
.video-frame{left:574px;top:1275px;width:465px;height:284px;background:linear-gradient(135deg,#5b5047,#2a2a2e 60%,#3c3f44)}
.play{left:767px;top:1373px;width:80px;height:80px;border-radius:50%;border:4px solid var(--white);background:rgba(0,0,0,.3)}

/* packages */
.package-bg{left:0;top:1655px;width:1200px;height:801px;background:linear-gradient(180deg,#e8edf2 0%,#f7f9fb 30%,#dfe4ea 60%,#c9d0d8 100%)}
.package-title{left:0;top:1733px;width:1200px;text-align:center;font-size:26px}
.tabs{left:436px;top:1811px;display:flex;gap:12px}
.tabs span{font-family:"Montserrat",sans-serif;font-size:10px;font-weight:600;padding:4px 8px}
.tabs .active{background:#222;color:var(--white)}
.plan{position:absolute;background:var(--card);color:var(--white);text-align:center}
.plan-name{height:46px;line-height:46px;font-family:"Lato",sans-serif;font-style:italic;font-weight:900;font-size:22px}
.plan-price{height:120px;position:relative}
.plan-price .amount{position:absolute;left:90px;top:22px;font-family:"Lato",sans-serif;font-style:italic;font-weight:900;font-size:54px}
.plan-price .amount sup{font-size:20px;vertical-align:top;margin-right:4px}
.plan-price .amount small{font-size:11px;font-weight:700;font-style:normal}
.plan-sub{margin-top:16px;font-family:"Lato",sans-serif;font-style:italic;font-weight:700;font-size:16px;padding-bottom:16px;border-bottom:1px solid var(--card-line)}
.plan ul{list-style:none}
.plan li{font-size:11px;height:43px;line-height:43px;border-bottom:1px solid var(--card-line)}
.plan li:last-child{border-bottom:none}
.plan-btn{margin-top:14px;width:104px;height:30px;line-height:30px;background:var(--green-dark);color:var(--white);font-size:11px;font-weight:700}

/* testimonials */
.testi-title{left:0;top:2497px;width:1200px;text-align:center;font-size:26px;font-weight:700}
.review{position:absolute;width:270px;top:2583px}
.avatar{position:absolute;left:0;top:0;width:52px;height:52px;border-radius:50%;background:linear-gradient(135deg,#8a6b55,#3d5a3d)}
.stars{position:absolute;left:66px;top:0;color:var(--star);font-size:12px;letter-spacing:1px}
.quote{position:absolute;left:66px;top:22px;width:200px;font-size:10px;line-height:15px;font-style:italic;color:var(--grey-text)}
.who{position:absolute;left:66px;top:114px;font-family:"Montserrat",sans-serif;font-size:11px;font-weight:600}
.role{position:absolute;left:66px;top:136px;font-size:10px;color:var(--grey-text)}
.arrow{font-size:22px;color:#555;top:2664px}
.testi-dots{left:586px;top:2754px;display:flex;gap:5px}
.testi-dots i{width:8px;height:8px;border-radius:50%;border:1px solid var(--green);display:block}
.testi-dots i.on{background:var(--green)}

/* booking */
.booking-bg{left:0;top:2823px;width:1200px;height:550px}
.booking-title{left:217px;top:2992px;color:var(--white);font-size:30px}
.booking-lead{left:220px;top:3043px;width:380px;color:#ddd;font-size:14px;line-height:22px}
.booking-copy{left:220px;top:3100px;width:380px;color:#bbb;font-size:12px;line-height:21px}
.booking-btn{left:218px;top:3216px;width:168px;height:44px;line-height:44px;background:var(--blue-dark);color:var(--white);font-size:16px}

/* footer */
.footer{left:0;top:3354px;width:1200px;height:189px;background:linear-gradient(180deg,#e8e8e8,#d4d4d4)}
.foot-brand{left:198px;top:3406px;width:116px;height:116px;border-radius:50%;background:#111;display:flex;align-items:center;justify-content:center}
.foot-brand span{font-family:"Montserrat",sans-serif;font-weight:700;font-size:16px;color:var(--white)}
.foot-nav{left:350px;top:3434px;display:flex;gap:30px}
.foot-nav a{font-family:"Montserrat",sans-serif;font-size:13px;font-weight:500;color:#111;text-decoration:none}
.copyright{left:350px;top:3470px;font-size:11px;color:var(--grey-text)}
.social{left:890px;top:3430px;display:flex;gap:6px}
.social i{display:block;width:28px;height:28px;border-radius:50%;background:#111}
</style>
</head>
<body>

<!-- hero -->
<div class="abs hero" role="img" aria-label="Rider with electric mountain bike on a hilltop overlooking a bay and forest"></div>
<svg class="abs" style="left:0;top:600px" width="1200" height="125" viewBox="0 0 1200 125" aria-hidden="true">
  <path d="M0 110 L60 95 L110 100 L170 80 L230 92 L300 70 L360 85 L430 60 L470 72 L520 55 L560 75 L620 40 L660 58 L720 20 L760 45 L820 35 L870 60 L930 45 L990 65 L1050 50 L1110 70 L1160 60 L1200 75 L1200 125 L0 125 Z" fill="#fff"/>
</svg>
<div class="abs topbar"></div>
<div class="abs brand"><span>TRAILWAKA</span></div>
<nav class="abs main-nav">
  <a href="#">HOME</a><a href="#">ABOUT US</a><a href="#">WHAT WE OFFER</a><a href="#">BOOKINGS</a><a href="#">CONTACT US</a>
</nav>
<h1 class="abs hero-title">ELECTRIC MOUNTAIN<br>BIKE TOURS IN NEW ZEALAND</h1>
<a class="abs pill hero-btn">Click here</a>
<div class="abs dots"><i class="off"></i><i></i><i></i><i></i></div>

<!-- about -->
<div class="abs fern" style="left:200px;top:800px;width:340px;height:380px;background:radial-gradient(ellipse at center,#bdbdbd 0%,rgba(255,255,255,0) 70%)" role="img" aria-label="Faint silver fern decoration"></div>
<div class="abs fern" style="left:900px;top:940px;width:300px;height:230px;background:radial-gradient(ellipse at center,#c6c6c6 0%,rgba(255,255,255,0) 70%)" role="img" aria-label="Faint silver fern decoration"></div>
<svg class="abs" style="left:560px;top:724px" width="80" height="36" viewBox="0 0 80 36" aria-hidden="true">
  <polyline points="2,34 28,8 40,20 52,6 78,34" fill="none" stroke="#1d8bf0" stroke-width="4"/>
</svg>
<h2 class="abs heading about-title">ABOUT US</h2>
<div class="abs about-copy">
  <p>mi quis lacus mollis aliquam viscelerisque mi tortor at ipsum cligula augue bibendum accumsan vestibulum ut commodo a mi Morbi ornare gravida elit integer congue</p>
  <p>Aapsum dui aliquet felis at cursus magna nisi nec elit Praesent elementum elit at tellus nec ultricies sit amet porttitor mattis enim in massa libero interdum nec blandit sed nulla in ullamcorper est eget tempor cursus neque mi consectetuer mi a ultricies massa est sed nisl Class aptent taciti sociosqu ad litora torquent per conubia nostra per incepto</p>
</div>
<a class="abs pill about-btn">Read More</a>

<!-- video -->
<svg class="abs video-band" width="1200" height="490" viewBox="0 0 1200 490" role="img" aria-label="Green hills landscape backdrop">
  <defs><linearGradient id="grass" x1="0" y1="0" x2="0" y2="1"><stop offset="0" stop-color="#17a324"/><stop offset=".5" stop-color="#1f8f2a"/><stop offset="1" stop-color="#157a1f"/></linearGradient></defs>
  <path d="M0 10 L80 2 L160 12 L260 0 L380 10 L500 4 L640 12 L760 2 L900 10 L1040 0 L1200 8 L1200 478 L1100 488 L980 476 L840 486 L700 474 L560 486 L420 476 L280 488 L140 476 L0 486 Z" fill="url(#grass)"/>
</svg>
<svg class="abs" style="left:205px;top:1268px" width="90" height="34" viewBox="0 0 90 34" aria-hidden="true">
  <polyline points="2,32 30,6 44,20 58,4 88,32" fill="none" stroke="#fff" stroke-width="4"/>
</svg>
<h2 class="abs heading video-title">WATCH OUR VIDEO</h2>
<p class="abs video-copy">penatibus et magnis dis parturient montes nascetur ridiculus mus in iaculis facilisis massa Etiam Suspendisse quam leo molestie sed luctus quis feugiat in pede Fusce tellus Sed metus augue convallis et vehicula ut pulvinar eu ante integer orci tellus</p>
<a class="abs pill video-btn">Click here</a>
<svg class="abs" style="left:558px;top:1262px" width="496" height="314" viewBox="0 0 496 314" aria-hidden="true">
  <polyline points="2,60 2,2 60,2" fill="none" stroke="#fff" stroke-width="3"/>
  <polyline points="436,312 494,312 494,254" fill="none" stroke="#fff" stroke-width="3"/>
</svg>
<div class="abs video-frame" role="img" aria-label="Video still of electric mountain bikes lined up in a workshop"></div>
<div class="abs play"></div>
<svg class="abs" style="left:795px;top:1395px" width="30" height="36" viewBox="0 0 30 36" aria-hidden="true"><path d="M2 2 L28 18 L2 34 Z" fill="#fff"/></svg>

<!-- packages -->
<div class="abs package-bg" role="img" aria-label="Snowy mountain range backdrop"></div>
<div class="abs" style="left:148px;top:1785px;width:94px;height:118px;border-radius:45% 45% 20% 20%;background:linear-gradient(180deg,#8a6b4a,#5d4530)" role="img" aria-label="Kiwi bird standing on the price card"></div>
<svg class="abs" style="left:565px;top:1700px" width="70" height="32" viewBox="0 0 70 32" aria-hidden="true">
  <polyline points="2,30 26,6 38,18 50,4 68,30" fill="none" stroke="#555" stroke-width="4"/>
</svg>
<h2 class="abs heading package-title">OUR PACKAGE</h2>
<div class="abs tabs"><span>BIKE RENTAL</span><span>GUIDED TOURS</span><span class="active">RECOMMENDED</span></div>

<div class="plan" style="left:177px;top:1901px;width:279px;height:511px">
  <div class="plan-name" style="background:var(--orange)">STARTER</div>
  <div class="plan-price" style="background:var(--orange-light);clip-path:polygon(0 0,100% 0,100% 82%,0 100%)"><div class="amount"><sup>$</sup>19<small> / MONTH</small></div></div>
  <div class="plan-sub">SINGLE PLACE TRAVEL</div>
  <ul><li>Lorem ipsum dolorst</li><li>At vero eos et accusamus</li><li>Nam libero tempore coluta</li><li>Excepteur sint occaecat</li><li>On the other had ensonce</li></ul>
  <a class="pill plan-btn">BOOK NOW</a>
</div>
<div class="plan" style="left:456px;top:1873px;width:279px;height:567px;z-index:1">
  <div class="plan-name" style="background:var(--standard)">STANDARD</div>
  <div class="plan-price" style="background:var(--standard-light);clip-path:polygon(0 0,100% 0,100% 100%,0 82%)"><div class="amount"><sup>$</sup>39<small> / MONTH</small></div></div>
  <div class="plan-sub">THREE PLACE TRAVEL</div>
  <ul><li>Nam libero tempore coluta</li><li>On the other had ensonce</li><li>Lorem ipsum dolorst</li><li>At vero eos et accusamus</li><li>Excepteur sint occaecat</li></ul>
  <a class="pill plan-btn" style="margin-top:42px">BOOK NOW</a>
</div>
<div class="plan" style="left:735px;top:1901px;width:279px;height:511px">
  <div class="plan-name" style="background:var(--ultimate)">ULTIMATE</div>
  <div class="plan-price" style="background:var(--ultimate-light);clip-path:polygon(0 0,100% 0,100% 100%,0 82%)"><div class="amount"><sup>$</sup>59<small> / MONTH</small></div></div>
  <div class="plan-sub">FIVE PLACE TRAVEL</div>
  <ul><li>Excepteur sint occaecat</li><li>Nam libero tempore coluta</li><li>At vero eos et accusamus</li><li>On the other had ensonce</li><li>Lorem ipsum dolorst</li></ul>
  <a class="pill plan-btn">BOOK NOW</a>
</div>

<!-- testimonials -->
<h2 class="abs heading testi-title">TESTIMONIALS</h2>
<div class="abs arrow" style="left:120px">&#8249;</div>
<div class="abs arrow" style="left:1072px">&#8250;</div>
<div class="review" style="left:184px">
  <div class="avatar" role="img" aria-label="Customer portrait"></div>
  <div class="stars">★★★★☆</div>
  <p class="quote">" At vero eos et accusamus et iustodio dignissimos ducimus qui blanditiispraesent lum voluptatum deleniti atque corrupti quos dolores quas molestias "</p>
  <div class="who">AROHA BENNETT</div><div class="role">Creative Manager, NZ</div>
</div>
<div class="review" style="left:472px">
  <div class="avatar" role="img" aria-label="Customer portrait"></div>
  <div class="stars">★★★★☆</div>
  <p class="quote">" At vero eos et accusamus et iustodio dignissimos ducimus qui blanditiispraesent lum voluptatum deleniti atque corrupti quos dolores quas molestias "</p>
  <div class="who">LIAM PARATA</div><div class="role">Events Manager, NZ</div>
</div>
<div class="review" style="left:763px">
  <div class="avatar" role="img" aria-label="Customer portrait"></div>
  <div class="stars">★★★★☆</div>
  <p class="quote">" At vero eos et accusamus et iustodio dignissimos ducimus qui blanditiispraesent lum voluptatum deleniti atque corrupti quos dolores quas molestias "</p>
  <div class="who">NINA CALLOWAY</div><div class="role">Sports Manager, NZ</div>
</div>
<div class="abs testi-dots"><i></i><i class="on"></i><i></i></div>

<!-- booking -->
<svg class="abs booking-bg" width="1200" height="550" viewBox="0 0 1200 550" role="img" aria-label="Mountain bike on a forest trail beside tree trunks">
  <defs><linearGradient id="forest" x1="0" y1="0" x2="1" y2="1"><stop offset="0" stop-color="#0d0f0c"/><stop offset=".5" stop-color="#1e2a16"/><stop offset=".75" stop-color="#4a5a2a"/><stop offset="1" stop-color="#2b2a24"/></linearGradient></defs>
  <path d="M0 60 L90 30 L170 52 L260 18 L340 44 L430 6 L520 40 L600 20 L690 48 L780 24 L860 44 L940 10 L1010 36 L1080 20 L1200 40 L1200 550 L0 550 Z" fill="url(#forest)"/>
</svg>
<div class="abs" style="left:1005px;top:2730px;width:150px;height:140px;border-radius:50% 50% 30% 30%;background:linear-gradient(180deg,#8a6b4a,#5d4530)" role="img" aria-label="Kiwi bird on a tree stump"></div>
<h2 class="abs heading booking-title">OUR BOOKING</h2>
<p class="abs booking-lead">Arnare gravida elit integer congue augue et malesuada iaculis ipsum dui aliquet felis at cursus ma</p>
<p class="abs booking-copy">libero interdum nec interdum vel blandit sed nulla in ullamcorper est eget tempor cursus neque mi consectetuer mi a ultricies massa est sed nisl Class aptent taciti sociosqu ad litora torquent per conubia nostra per</p>
<a class="abs pill booking-btn">Read More</a>

<!-- footer -->
<div class="abs footer"></div>
<div class="abs foot-brand"><span>TRAILWAKA</span></div>
<nav class="abs foot-nav"><a href="#">HOME</a><a href="#">ABOUT US</a><a href="#">WHAT WE OFFER</a><a href="#">BOOKINGS</a><a href="#">CONTACT US</a></nav>
<p class="abs copyright">© 2018 Company Name  All right reserved</p>
<div class="abs social"><i></i><i></i><i></i><i></i></div>

</body>
</html>
```